Sassy, natural personal lubricant knows that it is not always about the packaging

An opportunity exists to create packaging for the world's first Macadamia Oil personal lubricant - Warrabee Silk. Unlike any other personal lubricants, this product is created from pure macadamia nut oil. The fatty acids naturally occurring in Macadamia oil are highly anti-inflammatory and are the closest in composition to human skin lipids. Using Warrabee Silk in such a vulnerable part of our bodies is the safest and gentlest way to enhance sexual enjoyment while moisturizing and adding lubrication. Warrabee Silk is completely free of the parabens, glycerins, fragrances, hormones, silicones and petroleum products known to irritate the delicate vaginal wall.

Design tone for Warrabee Silk:
- intelligent, but not condescending or patronizing
- elegant and dignified but not prudish
- clean, natural, uninhibited

Design specs:
- See attached file for packaging specs

Colors:
- refer to www.warrabee.com to see other products in the range. This is a guide only. Use of those colors is not mandatory.

Ingredients:

100% Macadamia Oil

Additional features:

- edible
- vegan
- gluten-free
- low allergen
- naturally anti-microbial and anti-inflammatory

See http://thebarealchemist.com/benefits-of-macadamia-nut-oil-in-skin-care/ for a list of the benefits of macadamia oil.

Target Market(s)

Our target market are the early adopters within the baby boomer set. Their age is a badge of honor, they are comfortable in their own skin and as sensual and fun-loving as ever. They are in their prime - still cool, still curious, still a little crazy. They are open to new possibilities, just as they have been at every age and stage. They still have plenty to do and plenty to enjoy. Being pre-menopausal or menopausal, natural lubrication may be diminishing. Warrabee Silk is the completely natural way to bring back the pleasure in sex.

Requirements
Must have
• Brandname: Warrabee Silk

Container Packaging specs: http://www.kestrelvessel.com/images/art/4837K15-R-ELM-STAMPED.PDF
Dispenser: http://www.kestrelvessel.com/lotion-dispenser-pumps/p/xTQ720M/
Should not have
• No post-coital pictures
No people
Nothing phallic

```html
<!DOCTYPE html>
<html lang="en">
<head>
<meta charset="utf-8">
<title>Warrabee Silk – Label</title>
<link rel="stylesheet" href="https://fonts.googleapis.com/css2?family=Marcellus&family=Great+Vibes&display=swap">
<style>
  :root {
    --canvas-bg: #e4e4e1;
    --label-white: #fbfbf8;
    --plum: #5b1e4f;
    --plum-deep: #4a1640;
    --leaf-green: #9bb523;
    --leaf-green-soft: #c9d98a;
    --leaf-tint: rgba(175, 200, 110, 0.16);
  }
  * { box-sizing: border-box; margin: 0; padding: 0; }
  html, body {
    width: 1200px;
    height: 1000px;
    overflow: hidden;
    background: var(--canvas-bg);
  }
  .canvas {
    position: relative;
    width: 1200px;
    height: 1000px;
  }
  .label {
    position: absolute;
    left: 350px;
    top: 70px;
    width: 500px;
    height: 860px;
    background: var(--label-white);
    box-shadow: 0 6px 24px rgba(0, 0, 0, 0.12);
    overflow: hidden;
  }
  .band {
    position: absolute;
    left: 0;
    width: 100%;
    height: 26px;
    background: linear-gradient(
      to bottom,
      var(--leaf-green) 0 5px,
      var(--label-white) 5px 7px,
      var(--plum) 7px 19px,
      var(--label-white) 19px 21px,
      var(--leaf-green) 21px 26px
    );
  }
  .band--top { top: 0; }
  .band--bottom { bottom: 0; }
  .leaf-motif {
    position: absolute;
    left: 0;
    top: 200px;
    width: 100%;
    height: 630px;
    background: radial-gradient(ellipse at 60% 45%, var(--leaf-tint), rgba(255, 255, 255, 0) 70%);
  }
  .brand-mark {
    position: absolute;
    left: 50%;
    top: 60px;
    transform: translateX(-50%);
    width: 170px;
    height: 170px;
    border-radius: 50%;
    border: 6px solid var(--plum);
  }
  .text-line {
    position: absolute;
    left: 0;
    width: 100%;
    text-align: center;
    white-space: nowrap;
  }
  .brand-name {
    top: 268px;
    font-family: "Marcellus", serif;
    font-size: 78px;
    line-height: 1;
    color: var(--plum);
  }
  .product-name {
    top: 370px;
    font-family: "Great Vibes", cursive;
    font-size: 92px;
    line-height: 1;
    color: var(--leaf-green);
  }
  .claim {
    top: 555px;
    font-family: "Marcellus", serif;
    font-size: 38px;
    line-height: 1;
    color: var(--plum-deep);
  }
  .category {
    top: 608px;
    font-family: "Marcellus", serif;
    font-size: 31px;
    line-height: 1;
    color: var(--plum-deep);
  }
  .variant {
    top: 662px;
    font-family: "Great Vibes", cursive;
    font-size: 64px;
    line-height: 1;
    color: var(--plum);
  }
  .ingredient {
    top: 762px;
    font-family: "Marcellus", serif;
    font-size: 17px;
    letter-spacing: 0.5px;
    color: var(--plum-deep);
  }
  .volume {
    top: 790px;
    font-family: "Marcellus", serif;
    font-size: 17px;
    color: var(--plum-deep);
  }
</style>
</head>
<body>
  <main class="canvas">
    <section class="label">
      <div class="band band--top"></div>
      <div class="leaf-motif" role="img" aria-label="Faint line drawing of large lavender and macadamia leaves across the label"></div>
      <div class="brand-mark"></div>
      <p class="text-line brand-name">warrabee</p>
      <p class="text-line product-name">Silk</p>
      <p class="text-line claim">PURE &amp; NATURAL</p>
      <p class="text-line category">Personal lubricant</p>
      <p class="text-line variant">lavender</p>
      <p class="text-line ingredient">100% MACADAMIA OIL</p>
      <p class="text-line volume">8 oz 236.5ml</p>
      <div class="band band--bottom"></div>
    </section>
  </main>
</body>
</html>
```